Menu Design Project

My Restaurant is called The Platter Corner, it's fast food restaurant serves Gyro, Wings, Subs, Fried Seafood and chicken tenders. I'm looking for a menu design to fit the fast food category and have some photos of the food on the front page as well inside the menu. I will attached some photos and you can add any other photo related to the menu from the web.

Industry/Entity Type

Restaurant

```html
<!DOCTYPE html>
<html lang="en">
<head>
<meta charset="utf-8">
<title>The Platter Corner – Menu</title>
<link href="https://fonts.googleapis.com/css2?family=Montserrat:wght@600;700&family=Nunito+Sans:ital,wght@0,400;0,600;1,400;1,700&family=Pathway+Gothic+One&display=swap" rel="stylesheet">
<style>
  :root {
    --red: #e0141b;
    --red-dark: #b80d12;
    --blush: #fbe3e4;
    --paper: #ffffff;
    --ink: #1d1d1d;
    --stage: #e6e6e8;
  }
  * { box-sizing: border-box; margin: 0; padding: 0; }
  html, body { width: 1200px; height: 770px; overflow: hidden; background: var(--stage); }
  body { position: relative; font-family: "Nunito Sans", sans-serif; color: var(--ink); }

  .panel {
    position: absolute; width: 570px; height: 360px; background: var(--paper);
    overflow: hidden; box-shadow: 0 2px 8px rgba(0,0,0,.15);
  }
  .panel::before {
    content: ""; position: absolute; inset: 0;
    background:
      radial-gradient(ellipse 60% 45% at 30% 40%, var(--blush), transparent 70%),
      radial-gradient(ellipse 50% 40% at 75% 65%, var(--blush), transparent 70%);
  }
  .frame { position: absolute; inset: 10px; border: 3px solid var(--red); }
  .panel > * { z-index: 1; }
  .back { left: 20px; top: 20px; }
  .front { left: 20px; top: 390px; }
  .inside-top { left: 610px; top: 20px; }
  .inside-bottom { left: 610px; top: 390px; }
  .abs { position: absolute; }

  .tab {
    position: absolute; background: var(--red); color: #fff;
    font-family: "Montserrat", sans-serif; font-weight: 700; font-size: 12px;
    letter-spacing: .5px; text-transform: uppercase; padding: 3px 10px 3px 8px;
    display: flex; align-items: center; gap: 6px;
  }
  .tab .dot { width: 8px; height: 8px; border-radius: 50%; border: 2px solid #fff; }
  .tab small { font-size: 8px; }

  .list { position: absolute; list-style: none; font-size: 10.5px; line-height: 15px; }
  .list li { display: flex; justify-content: space-between; gap: 8px; }
  .list .price { white-space: nowrap; }
  .note { color: var(--red); font-size: 10.5px; }

  .photo { position: absolute; border-radius: 40%; }
  .photo.wings { background: radial-gradient(circle, #d8662a, #a23a12 70%, transparent 72%); }
  .photo.burger { background: radial-gradient(circle, #c9822f, #7a3b1a 68%, transparent 71%); }
  .photo.gyro { background: radial-gradient(circle, #9a5a35, #e7cf9e 66%, transparent 70%); }
  .photo.cans { background: linear-gradient(90deg, #c8141b, #3aa04a, #f08a18); border-radius: 8px; }
  .photo.meal { background: radial-gradient(circle, #e8b040, #c8141b 70%, transparent 72%); }
  .map { position: absolute; background: linear-gradient(135deg, #e9e9e9, #d2d2d2); border: 2px solid #888; border-radius: 16px; }

  .brand { font-family: "Montserrat", sans-serif; font-weight: 700; color: var(--ink); display: flex; align-items: center; gap: 8px; }
  .brand .mark { width: 14px; height: 14px; border-radius: 50%; background: var(--red); }

  .band {
    position: absolute; left: 10px; right: 10px; background: var(--red); color: #fff;
    font-family: "Montserrat", sans-serif; font-weight: 600; display: flex; align-items: center;
  }
  .contact { display: flex; align-items: center; gap: 6px; }
  .contact svg { width: 12px; height: 12px; fill: #fff; }
</style>
</head>
<body>

<!-- Outside back panel -->
<section class="panel back">
  <div class="frame"></div>
  <div class="band" style="top:13px;height:26px;justify-content:center;font-size:15px;letter-spacing:1.5px;">GOOD FOOD, GOOD MOOD</div>

  <div class="tab" style="left:35px;top:58px;"><span class="dot"></span>Drinks</div>
  <p class="abs" style="left:35px;top:86px;width:150px;font-size:10.5px;line-height:15px;">Cola, Diet Cola,<br>Lemon-Lime, Sports Drink,<br>Orange Soda,<br>Strawberry Soda,<br>Pepper Soda and more.</p>
  <div class="photo cans" role="img" aria-label="Photo of assorted soda cans" style="left:200px;top:60px;width:120px;height:85px;"></div>

  <div class="abs" style="left:160px;top:165px;width:200px;text-align:center;">
    <svg width="34" height="34" viewBox="0 0 34 34" aria-hidden="true"><path d="M3 10h28a14 14 0 0 1-28 0z" fill="#e0141b"/></svg>
    <p style="font-size:10px;">Call Us for Pick Up orders or Catering</p>
    <p style="font-size:11px;font-weight:700;font-style:italic;color:var(--red);">713-555-0186</p>
  </div>

  <div class="map" role="img" aria-label="Street map showing restaurant location" style="left:375px;top:100px;width:165px;height:140px;"></div>
  <p class="abs" style="left:375px;top:58px;width:165px;text-align:center;font-size:10.5px;">Hours of operation:<br><span style="color:var(--red);">Monday to Sunday 11am-9pm</span></p>

  <div class="abs" style="left:30px;right:30px;top:298px;border-top:1.5px solid #555;"></div>
  <div class="abs contact" style="left:40px;top:308px;font-size:11.5px;">
    <svg viewBox="0 0 12 12" style="fill:var(--red)"><path d="M6 0a4 4 0 0 0-4 4c0 3 4 8 4 8s4-5 4-8a4 4 0 0 0-4-4zm0 5.5A1.5 1.5 0 1 1 6 2.5a1.5 1.5 0 0 1 0 3z"/></svg>
    4817 Cedar Grove Blvd, Houston, TX 77045
    <svg viewBox="0 0 12 12" style="fill:var(--red);margin-left:14px"><path d="M2.5 0 4.5 2.6 3.3 4a7 7 0 0 0 4.7 4.7L9.4 7.5 12 9.5 10.3 12C5 12 0 7 0 1.7z"/></svg>
    713-555-0186
  </div>
</section>

<!-- Outside front cover -->
<section class="panel front">
  <div class="frame"></div>
  <div class="brand abs" style="left:0;right:0;top:50px;justify-content:center;font-size:16px;"><span class="mark"></span>The Platter Corner</div>
  <h1 class="abs" style="left:0;right:0;top:86px;text-align:center;font-family:'Pathway Gothic One',sans-serif;font-weight:400;font-size:36px;color:var(--red);">The Platter Corner Restaurant</h1>
  <p class="abs" style="left:0;right:0;top:140px;text-align:center;font-size:11px;line-height:18px;">Hours of operation:<br><span style="color:var(--red);">Monday to Sunday 11am-9pm</span></p>
  <div class="photo wings" role="img" aria-label="Photo of fried chicken wings" style="left:30px;top:200px;width:140px;height:100px;"></div>
  <div class="photo burger" role="img" aria-label="Photo of a cheeseburger" style="left:215px;top:195px;width:140px;height:105px;"></div>
  <div class="photo gyro" role="img" aria-label="Photo of a gyro wrap" style="left:400px;top:190px;width:145px;height:112px;"></div>
  <div class="band contact" style="bottom:13px;height:28px;justify-content:center;font-size:13px;gap:8px;">
    <svg viewBox="0 0 12 12"><path d="M6 0a4 4 0 0 0-4 4c0 3 4 8 4 8s4-5 4-8a4 4 0 0 0-4-4zm0 5.5A1.5 1.5 0 1 1 6 2.5a1.5 1.5 0 0 1 0 3z"/></svg>
    4817 Cedar Grove Blvd, Houston, TX 77045
    <svg viewBox="0 0 12 12" style="margin-left:12px"><path d="M2.5 0 4.5 2.6 3.3 4a7 7 0 0 0 4.7 4.7L9.4 7.5 12 9.5 10.3 12C5 12 0 7 0 1.7z"/></svg>
    713-555-0186
  </div>
</section>

<!-- Inside upper panel -->
<section class="panel inside-top">
  <div class="frame"></div>
  <div class="brand abs" style="left:0;right:0;top:38px;justify-content:center;font-size:12px;color:var(--red);"><span class="mark"></span>The Platter Corner Menu</div>

  <div class="tab" style="left:13px;top:62px;"><span class="dot"></span>Chicken</div>
  <ul class="list" style="left:35px;top:88px;width:180px;">
    <li><span>10 Large Wings</span><span class="price">$8.99</span></li>
    <li><span>20 Large Wings</span><span class="price">$16.99</span></li>
    <li><span>30 Large Wings</span><span class="price">$23.99</span></li>
    <li><span>50 Large Wings</span><span class="price">$39.99</span></li>
    <li><span>½ lb. Chicken Strips</span><span class="price">$5.49</span></li>
    <li><span>1lb. Chicken Strips</span><span class="price">$7.99</span></li>
    <li><span>½ lb. Gizzards</span><span class="price">$5.49</span></li>
    <li><span>1lb. Gizzards</span><span class="price">$7.99</span></li>
  </ul>
  <div class="tab" style="left:25px;top:218px;"><span class="dot"></span>Seafood</div>
  <ul class="list" style="left:45px;top:244px;width:170px;">
    <li><span>½ lb. Shrimp</span><span class="price">$7.99</span></li>
    <li><span>1lb. Shrimp</span><span class="price">$13.99</span></li>
    <li><span>½ lb. Fish</span><span class="price">$6.99</span></li>
    <li><span>1lb. Fish</span><span class="price">$12.99</span></li>
  </ul>

  <div class="tab" style="right:13px;top:62px;">Fresh Salad<span class="dot"></span></div>
  <ul class="list" style="left:260px;top:88px;width:285px;">
    <li><span>Caesar Salad</span><span class="price">$4.95</span></li>
    <li><span>Gyro Salad</span><span class="price">$5.95</span></li>
    <li><span>Shrimp Caesar Salad</span><span class="price">$6.25</span></li>
    <li><span>Greek Salad</span><span class="price">$5.95</span></li>
  </ul>
  <div class="tab" style="right:13px;top:160px;">Gyro &amp; Subs<span class="dot"></span></div>
  <ul class="list" style="left:260px;top:186px;width:285px;">
    <li><span>Gyro (Original or Chicken)</span><span class="price">$6.99</span></li>
    <li><span>¼ lb. Black Angus Burger</span><span class="price">$3.99</span></li>
    <li><span>Buffalo Chicken Sandwich</span><span class="price">$5.99</span></li>
    <li class="note">YOUR CHOICE OF 6" OR FOOTLONG SUBS</li>
    <li><span>Po Boy Shrimp</span><span class="price">$7.55-$9.25</span></li>
    <li><span>Philly (Steak or Chicken)</span><span class="price">$6.75-$8.99</span></li>
    <li><span>Fish</span><span class="price">$6.75-$8.99</span></li>
    <li><span>Turkey &amp; Cheese</span><span class="price">$6.49-$7.95</span></li>
  </ul>
</section>

<!-- Inside lower panel -->
<section class="panel inside-bottom">
  <div class="frame"></div>
  <div class="tab" style="left:13px;top:14px;"><span class="dot"></span>Sides</div>
  <ul class="list" style="left:30px;top:42px;width:190px;font-style:italic;">
    <li><span>French Fries</span><span class="price">$2.79</span></li>
    <li><span>Cajun Fries</span><span class="price">$3.99</span></li>
    <li><span>Onion Rings</span><span class="price">$4.99</span></li>
    <li><span>5 Jalapeno Poppers</span><span class="price">$4.99</span></li>
    <li><span>Fried Okra</span><span class="price">$4.99</span></li>
    <li><span>Fried Mushroom</span><span class="price">$5.49</span></li>
    <li><span>5 Mozzarella Sticks</span><span class="price">$5.49</span></li>
  </ul>

  <div class="tab" style="right:13px;top:14px;">Combos <small>Includes 16oz Soft Drink!</small><span class="dot"></span></div>
  <ul class="list" style="left:245px;top:42px;width:300px;font-style:italic;">
    <li><span>½ lb. Fish &amp; Fries</span><span class="price">$9.99</span></li>
    <li><span>½ lb. Shrimp &amp; Fries</span><span class="price">$10.99</span></li>
    <li><span>6" Philly (Steak or Chicken) &amp; Fries</span><span class="price">$9.99</span></li>
    <li><span>Gyro (Original, Chicken or Fish) &amp;Fries</span><span class="price">$9.49</span></li>
    <li><span>5 Wings &amp; Fries</span><span class="price">$9.49</span></li>
    <li><span>½ lb. Gizzards &amp; Fries</span><span class="price">$7.99</span></li>
    <li><span>¼ lb. Black Angus Burger &amp; Fries</span><span class="price">$6.99 <span style="color:var(--red);font-size:7px;">*CHEESE EXTRA</span></span></li>
    <li><span>5 Wings &amp; Gizzards</span><span class="price">$11.49</span></li>
    <li><span>½ lb. Chicken Strips &amp; Fries</span><span class="price">$7.99</span></li>
  </ul>

  <div class="photo meal" role="img" aria-label="Photo of nuggets, burger, fries and a soda" style="left:25px;top:195px;width:150px;height:110px;"></div>
  <div class="tab" style="left:215px;top:212px;">Kids Meal</div>
  <ul class="list" style="left:200px;top:240px;width:215px;font-style:italic;font-size:10px;">
    <li><span>Chicken Nuggets 4pc with small drink and fries</span><span class="price" style="color:var(--red);font-weight:700;">$4.95</span></li>
    <li><span>Chicken Strips 2pc with small drink and fries</span><span class="price" style="color:var(--red);font-weight:700;">$4.95</span></li>
    <li style="justify-content:center;gap:12px;"><span>Mac &amp; Cheese</span><span class="price" style="color:var(--red);font-weight:700;">$3.95</span></li>
  </ul>
  <div class="photo meal" role="img" aria-label="Photo of chicken strips, fries and a soda" style="left:425px;top:215px;width:125px;height:105px;"></div>
</section>

</body>
</html>
```